Natural Medicine & Health/Fitness Coaching studio requires web page

Require a innovative web page for a studio that coaches clients to better health, nutrition and fitness. The studio compromises of Clinical Nutritionists, Naturopaths, Rehab Trainers, Personal Trainers and Sport Coaches. Would like to see earthy but bold designs emphasizing nutritional health and athletic performance.
Updates

Design only launched today.

Target Market(s)

All genders from 20's to 60's, as well as families

Industry/Entity Type

Nutritionist

Coding

Coded - Design and coding required

Number of Pages Required

3 page

Colors
abd037
3277b5
fbee3d
fece3e
33b8a4
f04a50

Requirements
Must have
• Online booking system, ability to message
• Home page
• Coaching/Fitness page
• Nutritional Medicine page
• Must be suitable for both Fitness and Nutrition

```html
<!DOCTYPE html>
<html lang="en">
<head>
<meta charset="utf-8">
<title>Verdant Fit Nutritional Therapy</title>
<link href="https://fonts.googleapis.com/css2?family=Raleway:wght@400;500;600&family=Open+Sans:wght@400;600&display=swap" rel="stylesheet">
<style>
:root{
  --green:#abd037;
  --leaf:#4f9a2e;
  --blue:#3277b5;
  --navy:#1d4e7e;
  --footer:#14294a;
  --teal:#2ea98d;
  --yellow:#fece3e;
  --gold:#f7c531;
  --red:#f04a50;
  --text:#333;
  --muted:#666;
  --line:#d9d9d9;
}
*{margin:0;padding:0;box-sizing:border-box}
html,body{width:1200px;height:3689px;overflow:hidden;background:#fff}
body{font-family:'Open Sans',sans-serif;color:var(--text)}
.page{position:relative;width:1200px;height:3689px;overflow:hidden}
.abs{position:absolute}

/* header */
.brand{left:145px;top:44px;display:flex;align-items:center;gap:12px;font-family:'Raleway',sans-serif;font-weight:600;font-size:44px;color:var(--leaf)}
.brand-dot{width:26px;height:26px;border-radius:50%;background:var(--green)}
.phone{right:145px;top:28px;font-size:21px;font-weight:600;color:#222;display:flex;align-items:center;gap:8px}
.nav{top:80px;left:460px;display:flex;gap:0}
.nav a{font-family:'Open Sans',sans-serif;font-size:16px;color:#555;text-decoration:none;margin-right:36px}
.nav a.active{color:var(--red)}

/* hero */
.hero{left:0;top:130px;width:1200px;height:660px;background:linear-gradient(100deg,#d9cbb8 0%,#b9a38a 35%,#8e7259 60%,#c8b6a2 100%)}
.hero-card{left:720px;top:234px;width:335px;height:175px;background:var(--gold);padding:20px 22px;text-align:right}
.hero-card h1{font-family:'Raleway',sans-serif;font-weight:500;font-size:27px;line-height:34px;color:#222}
.hero-card p{font-size:11px;line-height:18px;color:#3a3a3a;margin-top:8px}
.arrow{width:38px;height:38px;border-radius:50%;background:var(--navy);display:flex;align-items:center;justify-content:center}

/* welcome */
.welcome-title{top:850px;left:0;width:1200px;text-align:center;font-family:'Raleway',sans-serif;font-weight:500;font-size:33px;color:var(--navy)}
.welcome-text{top:910px;left:145px;width:910px;text-align:center;font-size:14.5px;line-height:24px;color:#333}
.team{top:1011px;display:flex;flex-direction:column;align-items:center;width:190px}
.team-ring{width:142px;height:142px;border-radius:50%;border:3px solid var(--line);display:flex;align-items:center;justify-content:center}
.team-icon{width:60px;height:60px;border-radius:50%;background:linear-gradient(135deg,#bfe8df,#e9f3c9)}
.team-label{margin-top:12px;font-size:15px;color:var(--red)}

/* feature blocks */
.band{left:0;width:1200px;height:640px}
.feature-title{font-family:'Raleway',sans-serif;font-weight:500;font-size:33px}
.feature-title.on-teal{color:var(--yellow)}
.feature-title.on-white{color:var(--navy)}
.feature-text{width:458px;font-size:13.5px;line-height:24px}
.feature-text.on-teal{color:#fff}
.feature-text.on-white{color:#333}
.btn{width:104px;height:36px;background:var(--gold);color:#222;font-size:14px;font-weight:600;display:flex;align-items:center;justify-content:center;border-radius:2px}
.photo{width:392px;height:392px;border-radius:50%;border:8px solid var(--green);padding:5px;background:#fff}
.photo-fill{width:100%;height:100%;border-radius:50%}

/* booking */
.book-title{top:3125px;left:0;width:1200px;text-align:center;font-family:'Raleway',sans-serif;font-weight:500;font-size:33px;color:var(--navy)}
.field{height:40px;border:1px solid #c9c9c9;background:#f1f1f1;font-size:13px;color:#888;padding:0 12px;display:flex;align-items:center;justify-content:space-between}
.message{left:145px;top:3248px;width:910px;height:140px;border:1px solid #c9c9c9;background:#f1f1f1;font-size:13px;color:#888;padding:10px 12px}
.submit{left:548px;top:3410px;width:104px;height:38px;background:var(--gold);font-size:14px;font-weight:600;color:#222;display:flex;align-items:center;justify-content:center}

/* footer */
.footer-links{left:145px;top:3602px;font-size:12px;color:#fff;display:flex;gap:10px}
.copyright{left:145px;top:3638px;font-size:12px;color:#fff}
.social{top:3622px;display:flex;gap:20px;left:912px}
.social span{width:20px;height:20px;border-radius:50%;background:#fff}
.chat{left:1084px;top:3464px;width:80px;height:80px;border-radius:50%;background:var(--gold);display:flex;align-items:center;justify-content:center;box-shadow:0 3px 8px rgba(0,0,0,.2)}
</style>
</head>
<body>
<div class="page">

  <!-- header -->
  <div class="abs brand"><span class="brand-dot"></span>Verdant Fit</div>
  <div class="abs phone">
    <svg width="18" height="18" viewBox="0 0 24 24"><path fill="#222" d="M6.6 10.8a15.1 15.1 0 0 0 6.6 6.6l2.2-2.2c.3-.3.7-.4 1-.2 1.1.4 2.3.6 3.6.6.6 0 1 .4 1 1V20c0 .6-.4 1-1 1A17 17 0 0 1 3 4c0-.6.4-1 1-1h3.5c.6 0 1 .4 1 1 0 1.3.2 2.5.6 3.6.1.3 0 .7-.2 1z"/></svg>
    555 014 2290
  </div>
  <nav class="abs nav">
    <a class="active">Home</a><a>About Us</a><a>Coaching</a><a>Fitness</a><a>Nutrition</a><a>Contact Us</a>
  </nav>

  <!-- hero -->
  <div class="abs hero" role="img" aria-label="Couple preparing a fresh salad together in a bright kitchen"></div>
  <div class="abs arrow" style="left:55px;top:352px"><svg width="14" height="14" viewBox="0 0 14 14"><path d="M9 2 4 7l5 5" stroke="#fff" stroke-width="2.4" fill="none"/></svg></div>
  <div class="abs arrow" style="left:1105px;top:352px"><svg width="14" height="14" viewBox="0 0 14 14"><path d="M5 2l5 5-5 5" stroke="#fff" stroke-width="2.4" fill="none"/></svg></div>
  <div class="abs hero-card">
    <h1>HEALTH, NUTRITION<br>AND FITNESS</h1>
    <p>Eat well, move often and rest deeply. Our team guides every step of your journey to lasting strength and balance.</p>
  </div>
  <svg class="abs" style="left:0;top:660px" width="1200" height="140" viewBox="0 0 1200 140">
    <path d="M0 26 Q600 210 1200 26 L1200 140 L0 140 Z" fill="#fff"/>
    <path d="M0 22 Q600 206 1200 22" stroke="var(--green)" stroke-width="7" fill="none"/>
  </svg>

  <!-- welcome -->
  <h2 class="abs welcome-title">Welcome to Verdant Fit Nutritional Therapy</h2>
  <p class="abs welcome-text">We all know that healthy eating is important. The Mediterranean style of eating is possibly the most healthful dietary principle and is sometimes also called an "anti-inflammatory" diet. However, if we want to go a little further and make this more specific for healthy liver and gallbladder function,</p>
  <div class="abs team" style="left:124px"><div class="team-ring"><div class="team-icon" role="img" aria-label="Salad bowl icon"></div></div><div class="team-label">Clinical Nutritionists</div></div>
  <div class="abs team" style="left:313px"><div class="team-ring"><div class="team-icon" role="img" aria-label="Herbs in a jar icon"></div></div><div class="team-label">Naturopaths</div></div>
  <div class="abs team" style="left:503px"><div class="team-ring"><div class="team-icon" role="img" aria-label="Rehab exercise icon"></div></div><div class="team-label">Rehab Trainers</div></div>
  <div class="abs team" style="left:694px"><div class="team-ring"><div class="team-icon" role="img" aria-label="Personal trainer icon"></div></div><div class="team-label">Personal Trainers</div></div>
  <div class="abs team" style="left:884px"><div class="team-ring"><div class="team-icon" role="img" aria-label="Whistle icon"></div></div><div class="team-label">Sport Coaches</div></div>

  <!-- coaching band -->
  <svg class="abs band" style="top:1272px" viewBox="0 0 1200 640" aria-hidden="true">
    <path d="M0 0 Q600 132 1200 0 L1200 544 Q600 706 0 544 Z" fill="var(--blue)"/>
    <path d="M0 0 Q600 132 1200 0 L1200 530 Q600 692 0 530 Z" fill="var(--teal)"/>
  </svg>
  <h3 class="abs feature-title on-teal" style="left:145px;top:1430px">Coaching</h3>
  <p class="abs feature-text on-teal" style="left:145px;top:1486px">Maecenas vel tortor accumsan quam varius imperdiet vel eget elit. Aenean facilisis tincidunt lectus, id dictum nisi luctus eget. Vivamus efficitur ex condimentum, malesuada eros eget, feugiat nibh. Sed tellus ex, imperdiet eget gravida sit amet, volutpat eget turpis. In nec ultricies est. Etiam mattis augue vehicula odio posuere, sit amet tempus lectus luctus. Nulla facilisi. Etiam vel massa elementum, bibendum tellus venenatis, feugiat massa. Curabitur venenatis lacinia ornare.</p>
  <div class="abs btn" style="left:145px;top:1680px">Read More</div>
  <div class="abs photo" style="left:662px;top:1383px"><div class="photo-fill" role="img" aria-label="Two runners jogging along a seaside promenade" style="background:linear-gradient(180deg,#9fc4de 0%,#7fa7c2 45%,#c9b38e 70%,#a98b62 100%)"></div></div>

  <!-- fitness -->
  <div class="abs photo" style="left:143px;top:1968px"><div class="photo-fill" role="img" aria-label="Woman lifting red dumbbells outdoors" style="background:linear-gradient(160deg,#7a9a4a 0%,#5f7d38 40%,#c9453d 75%,#8d5a3c 100%)"></div></div>
  <h3 class="abs feature-title on-white" style="left:600px;top:2014px">Fitness</h3>
  <p class="abs feature-text on-white" style="left:600px;top:2070px">Maecenas vel tortor accumsan quam varius imperdiet vel eget elit. Aenean facilisis tincidunt lectus, id dictum nisi luctus eget. Vivamus efficitur ex condimentum, malesuada eros eget, feugiat nibh. Sed tellus ex, imperdiet eget gravida sit amet, volutpat eget turpis. In nec ultricies est. Etiam mattis augue vehicula odio posuere, sit amet tempus lectus luctus. Nulla facilisi. Etiam vel massa elementum, bibendum tellus venenatis, feugiat massa. Curabitur venenatis lacinia ornare.</p>
  <div class="abs btn" style="left:600px;top:2264px">Read More</div>

  <!-- nutrition band -->
  <svg class="abs band" style="top:2437px" viewBox="0 0 1200 640" aria-hidden="true">
    <path d="M0 0 Q600 132 1200 0 L1200 544 Q600 706 0 544 Z" fill="var(--blue)"/>
    <path d="M0 0 Q600 132 1200 0 L1200 530 Q600 692 0 530 Z" fill="var(--teal)"/>
  </svg>
  <h3 class="abs feature-title on-teal" style="left:145px;top:2595px">Nutrition</h3>
  <p class="abs feature-text on-teal" style="left:145px;top:2651px">Maecenas vel tortor accumsan quam varius imperdiet vel eget elit. Aenean facilisis tincidunt lectus, id dictum nisi luctus eget. Vivamus efficitur ex condimentum, malesuada eros eget, feugiat nibh. Sed tellus ex, imperdiet eget gravida sit amet, volutpat eget turpis. In nec ultricies est. Etiam mattis augue vehicula odio posuere, sit amet tempus lectus luctus. Nulla facilisi. Etiam vel massa elementum, bibendum tellus venenatis, feugiat massa. Curabitur venenatis lacinia ornare.</p>
  <div class="abs btn" style="left:145px;top:2845px">Read More</div>
  <div class="abs photo" style="left:662px;top:2548px"><div class="photo-fill" role="img" aria-label="Woman drinking a green smoothie" style="background:linear-gradient(170deg,#eceeea 0%,#d8dcd4 45%,#8a6a52 70%,#f4f4f2 100%)"></div></div>

  <!-- booking -->
  <h2 class="abs book-title">Book Now</h2>
  <div class="abs field" style="left:145px;top:3191px;width:216px">Name</div>
  <div class="abs field" style="left:376px;top:3191px;width:216px">Email</div>
  <div class="abs field" style="left:607px;top:3191px;width:217px">Phone</div>
  <div class="abs field" style="left:839px;top:3191px;width:216px">Service for<svg width="10" height="6" viewBox="0 0 10 6"><path d="M0 0h10L5 6z" fill="#444"/></svg></div>
  <div class="abs message">Message</div>
  <div class="abs submit">Submit</div>

  <!-- footer -->
  <svg class="abs" style="left:0;top:3480px" width="1200" height="209" viewBox="0 0 1200 209" aria-hidden="true">
    <path d="M0 10 Q600 80 1200 10 L1200 209 L0 209 Z" fill="var(--footer)"/>
  </svg>
  <div class="abs chat"><svg width="38" height="34" viewBox="0 0 38 34"><path d="M19 2C9 2 2 8 2 15.5c0 4 2 7.5 5.5 10L6 32l8-4c1.6.4 3.2.6 5 .6 10 0 17-6 17-13.1S29 2 19 2z" fill="var(--footer)"/></svg></div>
  <div class="abs footer-links"><span>Home</span><span>|</span><span>About Us</span><span>|</span><span>Coaching</span><span>|</span><span>Fitness</span><span>|</span><span>Nutrition</span><span>|</span><span>Contact Us</span></div>
  <div class="abs copyright">Copyright &copy; 2019 &nbsp;Verdant Fit Nutritional Therapy. &nbsp;All rights reserved</div>
  <div class="abs social" aria-label="Social links"><span></span><span></span><span></span><span></span></div>

</div>
</body>
</html>
```